Wine Shop Banners

Banner graphic/images required
Require banner images to match the present online wine shop.

www.korbel-tafelhaus.de

The wine-shop presently has a very clean, simple design, lots of white space, which is very much the trend at the moment.

Requirements
Images or graphic design for present banners visible on the homepage

The colour and feeling of the banners must fit in with the present clean, simple design.

Work required
3 large slide-card/banners (can be more) and 3 smaller fixed banners below. Please view website to see present position of banners.

LARGE BANNERS x 3

Something special with white background within the banner space
White background on each slide-card. Small individual graphic image in the middle of the slide card. This could be either a simple element of wine:
ingredients, fruit (grape), bottle, cork, old bottle label etc. just displaying one item on each slide-card. Preferably with high quality graphic features.

Note:
We are trying the steer away from the classic stereotype wineshop design. The image/s should have a higher, individual graphic touch, which gives the design something different. Sometimes such artistic work is displayed in steampunk or even in nostalgic design, which leaves the viewer slightly memorized with the content.
To clarify: we are not looking for a full steampunk design but possibly certain elements of this will give you an idea what we mean. That is to say, the design can go slightly in this direction without going over the top. Something small but very eye-catching.

SMALLER BANNERS x 3

One idea is:
Showing a symbol e.g. - discount sign "%" against a white background but again with a high graphic quality.

Target Market(s)

People interested in purchasing wine.
Ages approx. 25 to 65

Industry/Entity Type

Shop

Requirements
Must have
• Something special with white background
• Small individual graphic image in the middle of the slide card.
Nice to have
• The image/s should have a higher, individual graphic touch, which gives the design something different. Something that leaves the viewer slightly memorized with the content.
Should not have
• Not the typical classical design that is often seen on wine shops.

```html
<!DOCTYPE html>
<html lang="en">
<head>
<meta charset="utf-8">
<title>Special Offers – 20 % Off</title>
<link rel="stylesheet" href="https://fonts.googleapis.com/css2?family=Cinzel:wght@400;700&display=swap">
<style>
  :root {
    --canvas: #ffffff;
    --panel-edge: #ececec;
    --panel-centre: #ffffff;
    --tag-green: #5a8a3e;
    --tag-green-dark: #46702f;
    --gold: #f7b500;
    --gold-shade: #5a4300;
    --tag-text: #ffffff;
    --string: #8a8a8a;
  }
  html, body {
    margin: 0;
    padding: 0;
    width: 1200px;
    height: 900px;
    overflow: hidden;
    background: var(--canvas);
  }
  .canvas {
    position: relative;
    width: 1200px;
    height: 900px;
  }
  .banner {
    position: absolute;
    left: 60px;
    top: 140px;
    width: 1080px;
    height: 500px;
    background: radial-gradient(ellipse 62% 58% at 50% 50%, var(--panel-centre) 70%, var(--panel-edge) 100%);
  }
  .hanger {
    position: absolute;
    left: 0;
    top: 0;
    width: 1200px;
    height: 900px;
    pointer-events: none;
  }
  .price-tag {
    position: absolute;
    left: 58px;
    top: 248px;
    width: 290px;
    height: 360px;
    transform: rotate(18deg);
    background: radial-gradient(circle at 40% 35%, var(--tag-green) 0%, var(--tag-green-dark) 100%);
    box-shadow: 4px 6px 8px rgba(0,0,0,0.35);
    border-radius: 3px;
  }
  .price-tag__label {
    position: absolute;
    left: 0;
    top: 88px;
    width: 100%;
    margin: 0;
    text-align: center;
    font-family: "Cinzel", serif;
    font-weight: 700;
    font-size: 58px;
    line-height: 1.15;
    color: var(--tag-text);
    transform: rotate(8deg);
    text-shadow: 2px 2px 0 #555, 3px 4px 4px rgba(0,0,0,0.5);
  }
  .headline {
    position: absolute;
    left: 440px;
    top: 255px;
    width: 620px;
    margin: 0;
    text-align: center;
    font-family: "Cinzel", serif;
    font-weight: 400;
    font-size: 106px;
    line-height: 150px;
    color: var(--gold);
    text-shadow: -1px -1px 0 var(--gold-shade), 2px 2px 2px rgba(0,0,0,0.35);
  }
  .headline span { display: block; }
</style>
</head>
<body>
<main class="canvas">
  <section class="banner" aria-label="Special offers banner"></section>

  <svg class="hanger" viewBox="0 0 1200 900" aria-hidden="true">
    <defs>
      <radialGradient id="pin-shine" cx="0.4" cy="0.35" r="0.7">
        <stop offset="0" stop-color="#ffffff"/>
        <stop offset="1" stop-color="#9a9a9a"/>
      </radialGradient>
    </defs>
    <line x1="318" y1="178" x2="238" y2="238" stroke="var(--string)" stroke-width="4"/>
    <line x1="322" y1="180" x2="340" y2="278" stroke="var(--string)" stroke-width="4"/>
    <circle cx="320" cy="176" r="25" fill="url(#pin-shine)" stroke="#888" stroke-width="1"/>
  </svg>

  <div class="price-tag">
    <p class="price-tag__label">20 %<br>OFF</p>
  </div>

  <h1 class="headline"><span>SPECIAL</span><span>OFFERS</span></h1>
</main>
</body>
</html>
```